Meridale Bed Company Needs Business Card

Looking for a very nice looking business card. Creative but not extravagant. We sell beds and pillows across the U.S. and need something professional but catchy. I have attached the logo.

Name : Devin Holt
Title : President
Phone : (800) 471-2960
Email: sleep@quilmora.com
Website: www.quilmora.com

Can be single-sided or double-sided
horizontal or vertical

Can use Blues/Greys

Target Market(s)

Mass Market

Industry/Entity Type

Retail

Contact Information for Business Card

Name : Devin Holt
Title : President
Phone : (800) 471-2960
Email: sleep@quilmora.com
Website: www.quilmora.com

Requirements
Must have
• Clean, Modern, Smooth
• Can use Blues/Greys
• On the other side without the information - have something simple like www.quilmora.com or our logo
Nice to have
• Surprise me
Should not have
• Nothing crazy, nothing cluttered

```html
<!DOCTYPE html>
<html lang="en">
<head>
<meta charset="utf-8">
<title>Meridale Bed Company – Business Card</title>
<link rel="stylesheet" href="https://fonts.googleapis.com/css2?family=Open+Sans:wght@400;700&display=swap">
<style>
  :root {
    --page-bg: #ececec;
    --card-grey: #5b5b5b;
    --brand-blue: #2aa6de;
    --text-white: #ffffff;
  }
  * { margin: 0; padding: 0; box-sizing: border-box; }
  html, body {
    width: 1200px;
    height: 900px;
    overflow: hidden;
    background: var(--page-bg);
    font-family: "Open Sans", Arial, sans-serif;
  }
  .business-card {
    position: absolute;
    left: 145px;
    top: 190px;
    width: 910px;
    height: 520px;
    background: var(--card-grey);
    border-radius: 24px;
    box-shadow: 0 10px 30px rgba(0, 0, 0, 0.15);
    overflow: hidden;
  }
  .brand-name {
    position: absolute;
    right: 56px;
    top: 88px;
    font-weight: 700;
    font-size: 72px;
    line-height: 1;
    color: var(--brand-blue);
  }
  .holder {
    position: absolute;
    left: 46px;
    top: 270px;
  }
  .holder-name {
    font-weight: 700;
    font-size: 34px;
    line-height: 1.2;
    color: var(--brand-blue);
  }
  .holder-title {
    font-weight: 400;
    font-size: 28px;
    line-height: 1.2;
    color: var(--text-white);
  }
  .divider {
    position: absolute;
    left: 0;
    right: 0;
    top: 358px;
    height: 3px;
    background: var(--brand-blue);
  }
  .contact-list {
    position: absolute;
    right: 52px;
    top: 388px;
    list-style: none;
  }
  .contact-item {
    display: flex;
    align-items: center;
    justify-content: flex-end;
    gap: 12px;
    height: 38.5px;
    font-size: 24px;
    color: var(--text-white);
  }
  .contact-icon {
    width: 20px;
    height: 20px;
    fill: var(--brand-blue);
    flex: none;
  }
</style>
</head>
<body>
  <div class="business-card">
    <div class="brand-name">quilmora</div>

    <div class="holder">
      <div class="holder-name">Devin Holt</div>
      <div class="holder-title">President</div>
    </div>

    <div class="divider"></div>

    <ul class="contact-list">
      <li class="contact-item">
        <span>(800) 471-2960</span>
        <svg class="contact-icon" viewBox="0 0 20 20" aria-hidden="true">
          <path d="M5 2c1 0 1.6.4 2 1.3l1 2.3c.3.8.1 1.4-.5 1.9l-1 .8c.8 1.7 2 2.9 3.7 3.7l.8-1c.5-.6 1.1-.8 1.9-.5l2.3 1c.9.4 1.3 1 1.3 2v1.2c0 1-.8 1.8-1.8 1.8C8.6 17.5 2.5 11.4 2.5 4.3 2.5 3.3 3.3 2.5 4.3 2.5z"/>
        </svg>
      </li>
      <li class="contact-item">
        <span>sleep@quilmora.com</span>
        <svg class="contact-icon" viewBox="0 0 20 20" aria-hidden="true">
          <rect x="2" y="5" width="16" height="11" rx="1"/>
          <polyline points="2.5,5.5 10,11 17.5,5.5" fill="none" stroke="var(--card-grey)" stroke-width="1.4" stroke-linejoin="round"/>
        </svg>
      </li>
      <li class="contact-item">
        <span>www.quilmora.com</span>
        <svg class="contact-icon" viewBox="0 0 20 20" aria-hidden="true">
          <circle cx="10" cy="10" r="8.5"/>
          <path d="M6 5c2 0 3 1 2.5 2.5S6 9 7 11s2 1 2 3-1 2.5-1 2.5M12 4c-.5 1.5.5 2.5 2 2.5s2 1.5 1 3-2 1-2.5 2.5" fill="none" stroke="var(--card-grey)" stroke-width="1.3" stroke-linecap="round"/>
        </svg>
      </li>
    </ul>
  </div>
</body>
</html>
```